Business Card - connecting 2 souls and beggining the journey of self discovery

Logo on the front
with tag line

On the back list of services and contact details

Seminars
workshops
Coaching
podcasts

Darren Whitlow
Health & Wellbeing Life Coach
0491 372 615
darren@brightcoreliving.example
brightcoreliving.example

Industry/Entity Type

Life Coaching

Contact Information for Business Card

I like the use of colour from the logo to be used. I'm not a fan of white.

Requirements
Must have
• My tagline: The path inward begins with you
Nice to have
• Use of colour that is in the mind body soul logo

```html
<!DOCTYPE html>
<html lang="en">
<head>
<meta charset="utf-8">
<title>Bright Core Living – Business Card</title>
<link href="https://fonts.googleapis.com/css2?family=Open+Sans:wght@400;600;700&display=swap" rel="stylesheet">
<style>
  :root{
    --bg:#2a2a2c;
    --card:#ffffff;
    --ink:#3c3c3e;
    --grey:#7a7a7c;
    --purple:#6a4fa3;
    --teal:#2fa89a;
    --coral:#e8566a;
    --orange:#f08a3c;
    --green:#8cc63f;
    --spectrum:linear-gradient(90deg,var(--purple),var(--teal) 35%,var(--coral) 65%,var(--orange) 82%,var(--green));
  }
  *{margin:0;padding:0;box-sizing:border-box}
  html,body{width:1200px;height:1000px;overflow:hidden}
  body{background:var(--bg);font-family:"Open Sans",Arial,sans-serif;color:var(--ink);position:relative}
  .card{position:absolute;left:220px;width:760px;height:440px;background:var(--card);border-radius:22px;box-shadow:0 10px 30px rgba(0,0,0,.45)}
  .card--front{top:40px}
  .card--back{top:520px}

  .brand{display:flex;flex-direction:column;align-items:center}
  .brand__dot{width:96px;height:96px;border-radius:50%;background:var(--teal)}
  .brand__name{margin-top:14px;font-weight:600;font-size:34px;letter-spacing:-1px;color:var(--grey);white-space:nowrap}
  .card--front .brand{position:absolute;top:110px;left:0;right:0}
  .tagline{position:absolute;left:0;right:0;top:352px;text-align:center;font-size:16px;letter-spacing:4px;font-weight:600;white-space:nowrap}
  .tagline .t1{color:var(--purple)} .tagline .t2{color:var(--teal)}
  .tagline .t3{color:var(--coral)} .tagline .t4{color:var(--green)}

  .card--back .brand{position:absolute;top:42px;right:40px}
  .card--back .brand__dot{width:74px;height:74px}
  .card--back .brand__name{font-size:24px;margin-top:10px}

  .person{position:absolute;left:44px;top:192px}
  .person__name{font-size:32px;font-weight:700;letter-spacing:1px;text-transform:uppercase;background:var(--spectrum);-webkit-background-clip:text;background-clip:text;color:transparent;white-space:nowrap}
  .person__role{font-size:21px;font-weight:600;color:var(--grey);margin-top:-4px}
  .rule{position:absolute;left:44px;right:44px;top:276px;height:2px;background:var(--spectrum)}

  .contacts{position:absolute;left:44px;top:296px;list-style:none}
  .contacts li{display:flex;align-items:center;gap:12px;font-size:18px;line-height:30px;white-space:nowrap}
  .contacts svg{width:18px;height:18px;flex:none}
  .web__mid{background:var(--spectrum);-webkit-background-clip:text;background-clip:text;color:transparent}

  .services{position:absolute;right:44px;top:340px;text-align:right;font-size:19px;line-height:30px;color:var(--ink);white-space:nowrap}
</style>
</head>
<body>
  <section class="card card--front">
    <div class="brand">
      <div class="brand__dot"></div>
      <div class="brand__name">Bright Core Living</div>
    </div>
    <p class="tagline"><span class="t1">THE PATH</span> <span class="t2">INWARD</span> <span class="t3">BEGINS</span> <span class="t4">WITH YOU</span></p>
  </section>

  <section class="card card--back">
    <div class="brand">
      <div class="brand__dot"></div>
      <div class="brand__name">Bright Core Living</div>
    </div>
    <div class="person">
      <h1 class="person__name">Darren Whitlow</h1>
      <p class="person__role">Life Coach</p>
    </div>
    <div class="rule"></div>
    <ul class="contacts">
      <li><svg viewBox="0 0 18 18"><rect x="5" y="1" width="8" height="16" rx="2" fill="none" stroke="var(--purple)" stroke-width="1.6"/><circle cx="9" cy="14" r="1" fill="var(--purple)"/></svg>0491 372 615</li>
      <li><svg viewBox="0 0 18 18"><rect x="1" y="4" width="16" height="11" fill="var(--teal)"/><path d="M1 4l8 6 8-6" fill="none" stroke="#fff" stroke-width="1.4"/></svg>darren@brightcoreliving.example</li>
      <li><svg viewBox="0 0 18 18"><circle cx="9" cy="9" r="8" fill="var(--teal)"/><path d="M1 9h16M9 1c-4 4-4 12 0 16M9 1c4 4 4 12 0 16" fill="none" stroke="#fff" stroke-width="1.1"/></svg><span>www.<span class="web__mid">brightcoreliving</span>.example</span></li>
    </ul>
    <div class="services">
      <p>Seminars | Workshops</p>
      <p>Coaching | Podcasts</p>
    </div>
  </section>
</body>
</html>
```